Verdana Crest New Website - Online Learning and Education

New Wordpress website for an online learning site that has courses, worksheets, quizzes, etc.
Updates

We would like something similar to this website: https://hallowaybridgeinstitute.example/mediation-skills-course/. But continue with the content of our current website: http://verdanacrestlearninghub.example

We would like something similar to this site: https://hallowaybridgeinstitute.example/mediation-skills-course/

Coding

Coded - Design and coding required

```html
<!DOCTYPE html>
<html lang="en">
<head>
<meta charset="utf-8">
<title>Verdana Crest – Professional Courses &amp; Certifications</title>
<link href="https://fonts.googleapis.com/css2?family=Poppins:wght@500;600;700;800&family=Lato:wght@400;700&display=swap" rel="stylesheet">
<style>
:root{
  --red:#b3121d;
  --navy:#1c3f86;
  --navy-deep:#16336f;
  --ink:#1d1d1d;
  --text:#444;
  --muted:#777;
  --blush:#f5f0f0;
  --tile:#f3eeee;
  --dark:#2b2b2b;
  --white:#fff;
}
*{margin:0;padding:0;box-sizing:border-box}
html,body{width:1200px;height:4016px;overflow:hidden}
body{position:relative;background:var(--white);font-family:"Lato",sans-serif;color:var(--text)}
.abs{position:absolute}
h1,h2,h3,h4{font-family:"Poppins",sans-serif;color:var(--ink)}
.section-title{position:absolute;left:0;width:1200px;text-align:center;font-size:29px;font-weight:800;letter-spacing:-.3px}
.section-title::after{content:"";display:block;width:36px;height:3px;background:#999;margin:18px auto 0}

/* header */
.site-header{position:absolute;top:0;left:0;width:1200px;height:112px;background:#fff}
.brand{position:absolute;left:140px;top:26px;display:flex;align-items:center;gap:14px}
.brand-dot{width:48px;height:48px;border-radius:50%;background:var(--navy)}
.brand-name{font-family:"Poppins",sans-serif;font-weight:700;font-size:34px;color:var(--navy)}
.follow{position:absolute;top:26px;left:832px;display:flex;align-items:center;gap:8px;font-size:11px;font-family:"Poppins",sans-serif;font-weight:500;color:#333}
.social-dot{width:25px;height:25px;border-radius:50%}
.main-nav{position:absolute;top:72px;left:553px;display:flex;gap:36px;font-family:"Poppins",sans-serif;font-weight:600;font-size:12px;color:#222}
.main-nav .active{color:var(--red)}

/* hero */
.hero{position:absolute;top:112px;left:0;width:1200px;height:594px;background:linear-gradient(100deg,#f4f6f8 0%,#e7ecef 40%,#a8b6c0 70%,#8495a1 100%)}
.hero h1{position:absolute;left:204px;top:104px;font-size:31px;font-weight:600;line-height:42px;color:#151515}
.hero .lead{position:absolute;left:204px;top:206px;font-size:20px;color:#222}
.search{position:absolute;left:204px;top:270px;width:479px;height:59px;background:#fff;box-shadow:0 2px 6px rgba(0,0,0,.12);display:flex;align-items:center;padding:0 8px 0 24px;justify-content:space-between;font-size:14px;color:#333}
.search .btn{background:var(--red);color:#fff;font-family:"Poppins",sans-serif;font-weight:700;font-size:14px;padding:8px 20px}
.dots{position:absolute;left:0;width:1200px;display:flex;justify-content:center;gap:14px}
.dots span{width:10px;height:10px;border-radius:50%;background:#fff}
.dots .on{background:var(--red);box-shadow:0 0 0 2px #fff}

/* courses */
.course{position:absolute;width:234px;height:307px;background:#fff;box-shadow:0 2px 8px rgba(0,0,0,.13)}
.course .thumb{height:173px}
.course h3{position:absolute;left:20px;top:196px;font-size:14px;font-weight:700}
.course p{position:absolute;left:20px;top:218px;width:190px;font-size:12px;line-height:17px;color:#555}
.course .meta{position:absolute;left:0;bottom:0;width:100%;height:36px;border-top:1px solid #eee;display:flex;justify-content:space-between;align-items:center;padding:0 14px 0 18px;font-family:"Poppins",sans-serif;font-weight:600;font-size:9.5px;color:#333}
.meta i{display:inline-block;width:9px;height:9px;border-radius:50%;border:1.5px solid #777;margin-right:5px;vertical-align:-1px}

/* how it works */
.how{position:absolute;top:1583px;left:0;width:1200px;height:648px;background:var(--blush)}
.step{position:absolute;left:156px;width:390px}
.step svg{position:absolute;left:0;top:0}
.step h3{position:absolute;left:104px;top:0;font-size:19px;font-weight:600}
.step p{position:absolute;left:104px;top:34px;width:270px;font-size:14.5px;line-height:19.5px;color:#444}
.rule{position:absolute;left:145px;width:396px;height:1px;background:#ddd}

/* testimonials */
.testimonials{position:absolute;top:2231px;left:0;width:1200px;height:511px;background:linear-gradient(90deg,#1f4591 0%,#1b3f88 50%,#1d4190 100%)}
.testimonials .section-title{color:#fff}
.testimonials .section-title::after{background:#c8cfe0}
.quote-mark{position:absolute;font-family:"Poppins",sans-serif;font-size:64px;font-weight:800;color:#fff;line-height:1}
.quote{position:absolute;width:290px;font-size:16px;line-height:23px;color:#e6ebf6}
.person{position:absolute;display:flex;align-items:center;gap:18px}
.avatar{width:51px;height:51px;border-radius:50%;background:linear-gradient(#a9b2c0,#6d7686);border:2px solid #d5dbe6}
.person b{display:block;font-family:"Poppins",sans-serif;font-weight:600;font-size:15px;color:#fff}
.person span{font-size:13.5px;color:#c9d2e6}

/* categories */
.tile{position:absolute;width:183px;height:176px;background:var(--tile);text-align:center}
.tile svg{position:absolute;left:66px;top:30px}
.tile span{position:absolute;left:0;width:100%;top:112px;font-size:14.5px;line-height:19px;color:#333}
.btn-all{position:absolute;left:499px;top:3306px;width:202px;height:38px;background:var(--red);color:#fff;font-family:"Poppins",sans-serif;font-weight:700;font-size:13.5px;display:flex;align-items:center;justify-content:center}

/* stats */
.stats{position:absolute;top:3407px;left:0;width:1200px;height:214px;background:var(--dark)}
.stat{position:absolute;top:40px;width:200px;margin-left:-100px;text-align:center;color:#fff}
.stat svg{display:block;margin:0 auto 12px}
.stat b{display:block;font-family:"Poppins",sans-serif;font-weight:700;font-size:21px}
.stat span{display:block;font-size:15px;line-height:19px;color:#ddd;margin-top:4px}

/* footer */
.footer{position:absolute;top:3621px;left:0;width:1200px;height:395px;background:var(--navy)}
.foot-mark{position:absolute;left:134px;top:56px;width:290px;height:290px;border-radius:50%;border:3px solid rgba(255,255,255,.85);display:flex;align-items:center;justify-content:center;font-family:"Poppins",sans-serif;font-weight:700;font-size:26px;color:#fff}
.foot-col{position:absolute;top:56px;color:#fff}
.foot-col h4{font-family:"Poppins",sans-serif;font-weight:600;font-size:11.5px;color:#fff;margin-bottom:18px}
.foot-col li{list-style:none;font-size:13px;line-height:24px;color:#e1e7f3}
.contact-row{display:flex;gap:14px;font-size:13px;line-height:17px;color:#e1e7f3;margin-bottom:20px}
.connect li{display:flex;align-items:center;gap:12px;margin-bottom:14px;font-size:11.5px}
.connect .social-dot{width:26px;height:26px;background:#2a5cb8}
.foot-rule{position:absolute;left:413px;top:290px;width:643px;height:1px;background:rgba(255,255,255,.25)}
.copyright{position:absolute;right:144px;top:338px;font-size:11.5px;color:#e1e7f3}
</style>
</head>
<body>

<header class="site-header">
  <div class="brand"><div class="brand-dot"></div><div class="brand-name">Verdana Crest</div></div>
  <div class="follow">FOLLOW US
    <div class="social-dot" style="background:#3b5ca8;margin-left:6px"></div>
    <div class="social-dot" style="background:#1d9ae0"></div>
    <div class="social-dot" style="background:#1d2c52"></div>
    <svg width="18" height="18" viewBox="0 0 18 18" style="margin-left:24px"><circle cx="7.5" cy="7.5" r="5.5" fill="none" stroke="#333" stroke-width="2"/><line x1="11.5" y1="11.5" x2="16" y2="16" stroke="#333" stroke-width="2.4"/></svg>
  </div>
  <nav class="main-nav"><span class="active">HOME</span><span>ABOUT US</span><span>FEATURES</span><span>PRICING</span><span>BLOG</span><span>CONTACT US</span></nav>
</header>

<section class="hero">
  <div class="abs" role="img" aria-label="Photo of a smiling student with headphones studying at a laptop beside a potted plant" style="left:0;top:0;width:1200px;height:594px;background:linear-gradient(90deg,rgba(255,255,255,0) 45%,rgba(80,100,115,.25) 100%),radial-gradient(ellipse at 10% 90%,#8aa274 0%,rgba(138,162,116,0) 30%)"></div>
  <h1>PROFESSIONAL COURSES<br>&amp; CERTIFICATIONS</h1>
  <p class="lead">Advance Your Career, Now!</p>
  <div class="search"><span>SEARCH COURSE</span><span class="btn">SEARCH</span></div>
  <div class="dots" style="top:544px"><span></span><span></span><span class="on"></span><span></span><span></span></div>
</section>

<h2 class="section-title" style="top:757px">TRENDING COURSES</h2>

<article class="course" style="left:103px;top:870px"><div class="thumb" role="img" aria-label="Illustration of a laptop with code" style="background:linear-gradient(135deg,#4c5fe0,#2c36b0)"></div><h3>Lorem Ipsum is simply</h3><p>Lorem Ipsum is simply dummy text of the printing.</p><div class="meta"><span><i></i>214 LEARNERS</span><span><i></i>15 HRS</span></div></article>
<article class="course" style="left:358px;top:870px"><div class="thumb" role="img" aria-label="Illustration of a desk workspace with monitor" style="background:linear-gradient(135deg,#bff0f0,#8fdede)"></div><h3>Lorem Ipsum is simply</h3><p>Lorem Ipsum is simply dummy text of the printing.</p><div class="meta"><span><i></i>214 LEARNERS</span><span><i></i>15 HRS</span></div></article>
<article class="course" style="left:614px;top:870px"><div class="thumb" role="img" aria-label="Illustration of a glowing circuit board" style="background:radial-gradient(circle,#1f5a3c,#0a2418)"></div><h3>Lorem Ipsum is simply</h3><p>Lorem Ipsum is simply dummy text of the printing.</p><div class="meta"><span><i></i>214 LEARNERS</span><span><i></i>15 HRS</span></div></article>
<article class="course" style="left:868px;top:870px"><div class="thumb" role="img" aria-label="Illustration of a smartphone with neon interface" style="background:linear-gradient(135deg,#3a1a9a,#160a55)"></div><h3>Lorem Ipsum is simply</h3><p>Lorem Ipsum is simply dummy text of the printing.</p><div class="meta"><span><i></i>214 LEARNERS</span><span><i></i>15 HRS</span></div></article>

<article class="course" style="left:103px;top:1200px"><div class="thumb" role="img" aria-label="Illustration of web development icons around a monitor" style="background:linear-gradient(135deg,#4fd6c2,#2fbfae)"></div><h3>Lorem Ipsum is simply</h3><p>Lorem Ipsum is simply dummy text of the printing.</p><div class="meta"><span><i></i>214 LEARNERS</span><span><i></i>15 HRS</span></div></article>
<article class="course" style="left:358px;top:1200px"><div class="thumb" role="img" aria-label="Illustration of a rocket launching at night" style="background:linear-gradient(180deg,#261060,#6a2a9a)"></div><h3>Lorem Ipsum is simply</h3><p>Lorem Ipsum is simply dummy text of the printing.</p><div class="meta"><span><i></i>214 LEARNERS</span><span><i></i>15 HRS</span></div></article>
<article class="course" style="left:614px;top:1200px"><div class="thumb" role="img" aria-label="Illustration of a digital globe network" style="background:radial-gradient(circle,#2a5a78,#0c1a2c)"></div><h3>Lorem Ipsum is simply</h3><p>Lorem Ipsum is simply dummy text of the printing.</p><div class="meta"><span><i></i>214 LEARNERS</span><span><i></i>15 HRS</span></div></article>
<article class="course" style="left:868px;top:1200px"><div class="thumb" role="img" aria-label="Illustration of a person beside large browser windows" style="background:linear-gradient(135deg,#dceaf8,#a7c6ec)"></div><h3>Lorem Ipsum is simply</h3><p>Lorem Ipsum is simply dummy text of the printing.</p><div class="meta"><span><i></i>214 LEARNERS</span><span><i></i>15 HRS</span></div></article>

<section class="how">
  <h2 class="section-title" style="top:49px">HOW IT WORKS</h2>
  <div class="abs" role="img" aria-label="Photo of a smiling man with a headset working on a laptop" style="left:600px;top:151px;width:600px;height:497px;background:linear-gradient(135deg,#8c99a3,#5c6b76 55%,#c9ccc9)"></div>
</section>

<div class="step" style="top:1776px">
  <svg width="68" height="64" viewBox="0 0 68 64" fill="none" stroke="#b3121d" stroke-width="3.5"><path d="M10 6h46v48H18a8 8 0 0 1-8-8z"/><path d="M4 14h12"/><path d="M24 20l3 3 5-6M36 20h14M24 32l3 3 5-6M36 32h14M24 44l3 3 5-6M36 44h14"/></svg>
  <h3 style="top:10px">Coursework</h3>
  <p style="top:44px">Lorem ipsum dolor sit ame nsectetur adipiscing elit sed do eiusmod tempor incididunt ut labore.</p>
</div>
<div class="rule" style="top:1896px"></div>
<div class="step" style="top:1928px">
  <svg width="68" height="64" viewBox="0 0 68 64" fill="none" stroke="#b3121d" stroke-width="4"><path d="M10 44V32a24 24 0 0 1 48 0v12"/><rect x="6" y="36" width="12" height="22" rx="5" fill="#b3121d"/><rect x="50" y="36" width="12" height="22" rx="5" fill="#b3121d"/></svg>
  <h3 style="top:10px">Help &amp; Support</h3>
  <p style="top:44px">Lorem ipsum dolor sit ame nsectetur adipiscing elit sed do eiusmod tempor incididunt ut labore.</p>
</div>
<div class="rule" style="top:2053px"></div>
<div class="step" style="top:2082px">
  <svg width="68" height="64" viewBox="0 0 68 64" fill="none" stroke="#b3121d" stroke-width="3.5"><rect x="6" y="6" width="54" height="38" rx="2"/><path d="M16 16h34M16 24h18"/><circle cx="34" cy="44" r="7" fill="#b3121d"/><path d="M29 50l-2 10 7-4 7 4-2-10"/></svg>
  <h3 style="top:10px">Certificates</h3>
  <p style="top:44px">Lorem ipsum dolor sit ame nsectetur adipiscing elit sed do eiusmod tempor incididunt ut labore.</p>
</div>

<section class="testimonials">
  <div class="abs" role="img" aria-label="Faint background photo of students in a classroom" style="left:0;top:0;width:1200px;height:511px;background:radial-gradient(ellipse at 15% 30%,rgba(255,255,255,.06),rgba(255,255,255,0) 40%),radial-gradient(ellipse at 85% 60%,rgba(255,255,255,.06),rgba(255,255,255,0) 40%)"></div>
  <h2 class="section-title" style="top:50px">TESTIMONIALS</h2>
  <div class="quote-mark" style="left:165px;top:158px">“</div>
  <p class="quote" style="left:212px;top:178px">Sed ut perspiciatis unde omnis iste natus error sit voluptatem accus antium dolor emque laudantium, totam rem aperiam, eaque ipsa quae ab illo inventore veritatis.</p>
  <div class="person" style="left:209px;top:328px"><div class="avatar"></div><div><b>RICHARD</b><span>England</span></div></div>
  <div class="abs" style="left:600px;top:169px;width:1px;height:163px;background:rgba(255,255,255,.25)"></div>
  <div class="quote-mark" style="left:721px;top:158px">“</div>
  <p class="quote" style="left:767px;top:178px">But I must explain to you how all this mistaken idea of denouncing pleasure and praising pain was born and I will give you a complete account of the system, and expound.</p>
  <div class="person" style="left:765px;top:328px"><div class="avatar"></div><div><b>RICHARD</b><span>England</span></div></div>
  <div class="dots" style="top:453px;gap:12px"><span style="width:7px;height:7px;background:#3b62b0"></span><span style="width:7px;height:7px;background:#3b62b0"></span><span style="width:8px;height:8px;background:#fff"></span><span style="width:7px;height:7px;background:#3b62b0"></span><span style="width:7px;height:7px;background:#3b62b0"></span></div>
</section>

<h2 class="section-title" style="top:2797px">CATEGORIES</h2>

<div class="tile" style="left:134px;top:2898px"><svg width="54" height="54" viewBox="0 0 54 54" fill="#1c3f86"><path d="M8 20h10l20-12v38L18 34H8z"/><rect x="12" y="34" width="7" height="12"/><path d="M44 18a10 10 0 0 1 0 18" fill="none" stroke="#1c3f86" stroke-width="3"/></svg><span>Marketing<br>Management</span></div>
<div class="tile" style="left:321px;top:2898px"><svg width="54" height="54" viewBox="0 0 54 54" fill="#1c3f86"><circle cx="28" cy="12" r="10"/><text x="28" y="17" font-size="14" font-family="Lato,sans-serif" font-weight="700" fill="#fff" text-anchor="middle">$</text><path d="M4 40l10-10h12l8 4h12v4H32l-8 8H4z"/></svg><span>Finance<br>Management</span></div>
<div class="tile" style="left:508px;top:2898px"><svg width="54" height="54" viewBox="0 0 54 54"><circle cx="27" cy="27" r="16" fill="none" stroke="#1c3f86" stroke-width="8" stroke-dasharray="6 4.5"/><circle cx="27" cy="27" r="9" fill="#1c3f86"/><circle cx="27" cy="24" r="3" fill="#fff"/></svg><span>Business<br>Adminstration</span></div>
<div class="tile" style="left:695px;top:2898px"><svg width="54" height="54" viewBox="0 0 54 54"><path d="M27 46L8 27a11 11 0 0 1 19-15 11 11 0 0 1 19 15z" fill="#1c3f86"/><path d="M8 28h11l4-7 5 12 4-7h14" fill="none" stroke="#fff" stroke-width="2.5"/></svg><span>Healthcare</span></div>
<div class="tile" style="left:881px;top:2898px"><svg width="54" height="54" viewBox="0 0 54 54" fill="none" stroke="#1c3f86" stroke-width="3.5"><rect x="9" y="16" width="36" height="30"/><path d="M19 16V10a8 8 0 0 1 16 0v6"/><path d="M21 28v6a6 6 0 0 0 12 0v-6"/></svg><span>E commerce</span></div>

<div class="tile" style="left:134px;top:3079px"><svg width="54" height="54" viewBox="0 0 54 54"><circle cx="34" cy="18" r="10" fill="none" stroke="#1c3f86" stroke-width="7" stroke-dasharray="4 3"/><circle cx="16" cy="38" r="8" fill="none" stroke="#1c3f86" stroke-width="6" stroke-dasharray="3.5 3"/></svg><span>Service Excellence</span></div>
<div class="tile" style="left:321px;top:3079px"><svg width="54" height="54" viewBox="0 0 54 54" fill="#1c3f86"><circle cx="27" cy="14" r="10"/><rect x="19" y="10" width="16" height="5" fill="#fff"/><path d="M10 50V36a10 10 0 0 1 10-10h14a10 10 0 0 1 10 10v14z"/><rect x="20" y="34" width="14" height="10" fill="#fff"/></svg><span>IT Project</span></div>
<div class="tile" style="left:508px;top:3079px"><svg width="54" height="54" viewBox="0 0 54 54" fill="#1c3f86"><circle cx="27" cy="14" r="10"/><path d="M6 50a21 21 0 0 1 42 0z"/></svg><span>Human Resource</span></div>
<div class="tile" style="left:695px;top:3079px"><svg width="54" height="54" viewBox="0 0 54 54"><circle cx="27" cy="27" r="22" fill="#1c3f86"/></svg><span>CRM Suite</span></div>
<div class="tile" style="left:881px;top:3079px"><span>Data Science</span></div>

<div class="btn-all">VIEW ALL CATEGORIES</div>

<section class="stats">
  <div class="stat" style="left:203px"><svg width="44" height="44" viewBox="0 0 44 44" fill="#fff"><circle cx="12" cy="8" r="5"/><circle cx="32" cy="8" r="5"/><circle cx="22" cy="13" r="5"/><rect x="6" y="15" width="12" height="18" rx="3"/><rect x="26" y="15" width="12" height="18" rx="3"/><rect x="16" y="20" width="12" height="22" rx="3"/></svg><b>500K+</b><span>Students<br>Community</span></div>
  <div class="stat" style="left:391px"><svg width="44" height="44" viewBox="0 0 44 44"><circle cx="22" cy="22" r="17" fill="#fff"/><path d="M12 14c6 0 6 6 10 6s2 8-2 8-4 6-6 8M28 8c0 6 6 4 8 10" fill="none" stroke="#2b2b2b" stroke-width="3"/></svg><b>214</b><span>Countries<br>World Wide</span></div>
  <div class="stat" style="left:584px"><svg width="44" height="44" viewBox="0 0 44 44" fill="#fff"><path d="M10 4h18l8 8v28H10z"/><path d="M28 4v8h8" fill="#ccc"/></svg><b>1500+</b><span>Hours of<br>Content</span></div>
  <div class="stat" style="left:801px"><svg width="44" height="44" viewBox="0 0 44 44" fill="none" stroke="#fff" stroke-width="3"><rect x="7" y="9" width="30" height="29"/><path d="M7 17h30M14 4v9M30 4v9"/></svg><b>100+</b><span>Hours of Content<br>Added Every Week</span></div>
  <div class="stat" style="left:1006px"><svg width="44" height="44" viewBox="0 0 44 44" fill="#fff"><path d="M22 4l5.3 11.6 12.7 1.3-9.5 8.6 2.7 12.5L22 31.6 10.8 38l2.7-12.5L4 16.9l12.7-1.3z"/></svg><b>5000+</b><span>Positive<br>Reviews</span></div>
</section>

<footer class="footer">
  <div class="foot-mark">Verdana Crest</div>
  <div class="foot-col" style="left:418px">
    <h4>CONTACT US</h4>
    <div class="contact-row"><span>●</span><span>Blk 48 Marlow Grove Ave #02-115<br>&nbsp;&nbsp;&nbsp;Eastport 410278</span></div>
    <div class="contact-row"><span>✆</span><span>6120 4398</span></div>
    <div class="contact-row"><span>✉</span><span>hello@verdanacrest.example</span></div>
  </div>
  <div class="foot-col" style="left:724px">
    <h4>MENU</h4>
    <ul><li>HOME</li><li>ABOUT US</li><li>FEATURES</li><li>PRICING</li><li>BLOG</li><li>CONTACT US</li></ul>
  </div>
  <div class="foot-col connect" style="left:941px">
    <h4>CONNECT WITH US</h4>
    <ul><li><span class="social-dot"></span>Friendsphere</li><li><span class="social-dot"></span>Chirpline</li><li><span class="social-dot"></span>Worknet</li></ul>
  </div>
  <div class="foot-rule"></div>
  <div class="copyright">Copyrights @ 2019 All Rights Reserved</div>
</footer>

</body>
</html>
```